Animal Horse & Bedding Company Needs a Website Coded & Designed

We need a website for a new animal bedding and feed company that is visually grabbing and vibrant. We would like to see a website that displays trust, quality and confidence. Needs to be responsive and mobile friendly for all browsers and coded for both Android & IOS. SEO is also important.

Joomla or Wordpress – must be both desktop and mobile friendly with fast page load speed. Need the ability to edit ourselves in Wordpress or Joomla.

Full details attached below with some layout and content ideas.

Coding

Coded - Design and coding required

Number of Pages Required

5+ page

Font styles to use
Sans Serif

Requirements
Must have
• Needs to be responsive and mobile friendly for all browsers and coded for both Android & IOS. SEO is also important.

Wordpress – must be both desktop and mobile friendly with fast page load speed. Need the ability to edit ourselves in Wordpress.

Logo Colours:
Dark Brown
CMYK: 50 / 70 / 80 / 70
Pantone: 4625C

Orange
CMYK: 0 / 50 / 100 / 0
Pantone: 144C
Nice to have
• Use picture of building attached and super impose logo on building.

```html
<!DOCTYPE html>
<html lang="en">
<head>
<meta charset="utf-8">
<title>Goldfield Bedding – Request a Quote</title>
<link rel="stylesheet" href="https://fonts.googleapis.com/css2?family=Montserrat:wght@300;400;500;600;700&display=swap">
<style>
:root{
  --orange:#f7941d;
  --brown:#3b2314;
  --ink:#111111;
  --text:#555555;
  --muted:#8a8a8a;
  --line:#d9d9d9;
  --soft:#f4f4f4;
  --white:#ffffff;
  --shade:rgba(0,0,0,.78);
}
*{box-sizing:border-box;margin:0;padding:0}
html,body{width:1200px;height:3576px;overflow:hidden}
body{position:relative;font-family:'Montserrat',sans-serif;color:var(--text);background:var(--white)}
.abs{position:absolute}
/* header */
.site-header{left:0;top:0;width:1200px;height:62px;background:var(--white)}
.brand{left:171px;top:14px;display:flex;align-items:center;gap:10px;font-weight:600;font-size:19px;color:var(--brown);letter-spacing:1px}
.brand-dot{width:30px;height:30px;border-radius:50%;background:var(--orange)}
.nav{left:546px;top:24px;display:flex;gap:0;font-size:12.5px;color:var(--text)}
.nav a{text-decoration:none;color:inherit;position:absolute;white-space:nowrap}
.nav a.active{color:var(--orange)}
.nav a.active:after{content:"";position:absolute;left:10px;right:10px;bottom:-7px;height:2px;background:var(--orange)}
.btn{background:var(--orange);color:var(--white);font-size:11px;font-weight:500;display:flex;align-items:center;justify-content:center;border-radius:2px}
/* hero */
.hero{left:0;top:62px;width:1200px;height:490px;background:linear-gradient(120deg,#5b4a32,#3a3023 55%,#2a2219)}
/* features */
.features{left:0;top:552px;width:1200px;height:253px;background:var(--soft)}
.feature{width:230px;text-align:center}
.feature svg{display:block;margin:0 auto}
.feature h3{font-size:15px;font-weight:600;color:var(--ink);margin-top:14px}
.feature p{font-size:9.5px;color:var(--muted);line-height:1.35;margin-top:6px}
.divider{width:1px;height:100px;background:var(--line);top:640px}
/* sections */
.photo{border-radius:3px}
.eyebrow{font-size:15px;font-weight:300;color:var(--text)}
.title{font-size:25px;font-weight:700;color:var(--ink)}
.body{font-size:9.5px;line-height:1.6;color:var(--muted)}
.list{list-style:none;font-size:9.5px;color:var(--muted)}
.list li{height:20px;padding-left:22px;position:relative}
.list li:before{content:"›";position:absolute;left:0;color:var(--orange)}
.band{left:0;top:1366px;width:1200px;height:562px;background:var(--soft)}
/* products */
.card{top:2462px;height:256px;text-align:center;border:1px solid #eeeeee;background:var(--white)}
.card .pack{width:88px;height:110px;margin:36px auto 0;background:linear-gradient(#5a5a5a,#2b2b2b);border-radius:4px}
.card h4{font-size:14px;font-weight:500;color:var(--ink);margin-top:24px}
.stars{color:var(--orange);font-size:11px;letter-spacing:2px;margin-top:2px}
.price{font-size:14px;font-weight:600;color:var(--ink);margin-top:10px}
.card.hover{background:var(--orange);border-color:var(--orange);border-radius:6px}
.card.hover h4,.card.hover .price,.card.hover .stars{color:rgba(255,255,255,.35)}
.card.hover .pack{opacity:.15}
.zoom{left:50%;top:90px;margin-left:-28px;width:56px;height:56px;border-radius:50%;background:var(--white)}
.arrow{font-size:22px;color:#bbbbbb}
/* testimonial */
.clients{left:0;top:2834px;width:1200px;height:419px;background:linear-gradient(100deg,#6d5a45,#4a3c2e 50%,#7a6550);text-align:center;color:var(--white)}
.clients h2{font-size:25px;font-weight:700;margin-top:103px}
.clients .who{font-size:15px;margin-top:24px;color:var(--orange)}
.clients .role{font-size:10px;margin-top:4px}
.clients .quote{font-size:10px;line-height:1.55;width:490px;margin:20px auto 0}
.dots{display:flex;gap:6px;justify-content:center;margin-top:24px}
.dots span{width:9px;height:9px;border-radius:50%;border:1.5px solid var(--white)}
.dots span.on{background:var(--white)}
/* footer */
.footer h5{font-size:14px;font-weight:500;color:var(--ink)}
.footer .links{font-size:9.5px;color:var(--muted);line-height:21px;margin-top:10px}
.social{display:flex;gap:12px}
.social span{width:9px;height:9px;border-radius:50%;background:var(--orange)}
.field-sm{border:1px solid #eeeeee;height:21px;font-size:8.5px;color:#bbbbbb;padding:6px 26px}
.copy{left:0;top:3538px;width:1200px;text-align:center;font-size:8.5px;color:var(--muted)}
/* overlay & modal */
.shade{left:0;top:0;width:1200px;height:3576px;background:var(--shade)}
.modal{left:172px;top:93px;width:854px;height:430px;background:var(--white);border-radius:10px}
.modal h2{position:absolute;left:0;width:100%;top:36px;text-align:center;font-size:24px;font-weight:700;color:var(--ink)}
.input{border:1px solid var(--line);border-radius:3px;font-size:9px;color:#9a9a9a;padding:13px 15px}
.close{left:816px;top:15px}
</style>
</head>
<body>

<header class="site-header abs">
  <div class="brand abs"><span class="brand-dot"></span>GOLDFIELD BEDDING</div>
  <nav class="nav abs">
    <a class="active" href="#" style="left:0">Home</a>
    <a href="#" style="left:70px">About Us</a>
    <a href="#" style="left:157px">Feed</a>
    <a href="#" style="left:218px">Bedding</a>
    <a href="#" style="left:301px">Contact</a>
  </nav>
  <div class="btn abs" style="left:922px;top:18px;width:104px;height:26px;font-size:12px">Get a Quote</div>
</header>

<section class="hero abs" role="img" aria-label="Horse grazing beside a wooden paddock fence at dusk"></section>

<section class="features abs">
  <div class="feature abs" style="left:190px;top:62px">
    <svg width="54" height="60" viewBox="0 0 54 60"><circle cx="27" cy="24" r="20" fill="none" stroke="#f7941d" stroke-width="5"/><path d="M18 24l6 6 12-12" fill="none" stroke="#f7941d" stroke-width="4"/><path d="M14 40l-5 16 9-4 5 7 4-13M40 40l5 16-9-4-5 7-4-13" fill="#f7941d"/></svg>
    <h3>Quality Guaraanteed</h3>
    <p>Grown for quality, 100% natural with<br>no chemicals or additives.</p>
  </div>
  <div class="divider abs" style="left:446px"></div>
  <div class="feature abs" style="left:484px;top:62px">
    <svg width="58" height="58" viewBox="0 0 58 58"><g fill="#f7941d"><circle cx="29" cy="29" r="21"/><rect x="24" y="2" width="10" height="54" rx="2"/><rect x="2" y="24" width="54" height="10" rx="2"/><rect x="24" y="2" width="10" height="54" rx="2" transform="rotate(45 29 29)"/><rect x="24" y="2" width="10" height="54" rx="2" transform="rotate(-45 29 29)"/></g><circle cx="29" cy="29" r="9" fill="#f4f4f4"/></svg>
    <h3>Full Service Solution</h3>
    <p>Dedicated to providing a full service solution<br>of bedding supply &amp; waste removal.</p>
  </div>
  <div class="divider abs" style="left:746px"></div>
  <div class="feature abs" style="left:777px;top:62px">
    <svg width="60" height="58" viewBox="0 0 60 58"><g fill="#f7941d"><path d="M14 12h14l-3 6c9 5 11 16 11 24 0 9-6 12-15 12S6 51 6 42c0-8 3-19 11-24z"/><rect x="36" y="24" width="20" height="6" rx="2"/><rect x="36" y="33" width="20" height="6" rx="2"/><rect x="36" y="42" width="20" height="6" rx="2"/><rect x="36" y="51" width="20" height="6" rx="2"/></g><text x="21" y="46" font-family="Montserrat,sans-serif" font-size="16" font-weight="700" fill="#f4f4f4" text-anchor="middle">$</text></svg>
    <h3>Convenient &amp; Cost Effective</h3>
    <p>Compressed bags, pellets or bulk products<br>saving in shipping cost.</p>
  </div>
</section>

<section class="welcome">
  <div class="photo abs" style="left:172px;top:906px;width:366px;height:365px;background:linear-gradient(#8b8a7a,#3c3a33 60%,#5a4a38)" role="img" aria-label="Dairy cows feeding in an open barn"></div>
  <div class="eyebrow abs" style="left:588px;top:940px">Welcome to</div>
  <h2 class="title abs" style="left:588px;top:960px">Goldfield Bedding</h2>
  <div class="body abs" style="left:588px;top:1008px;width:438px">
    <p>Goldfield Bedding is a locally owned company located in Millbrook. We are dedicated to providing high quality products and services. Producing, baling and marketing hay and straw for a number of years, we rely on dependable teams of key staff members.</p>
    <p style="margin-top:15px">Goldfield Bedding offers supply and delivery of fresh bedding as well as removal of waste bedding. Let us deliver you a container of fresh straw and haul your waste bedding away. A full service solution that is sustainable and responsible.</p>
    <p style="margin-top:15px">Your animal deserves the very best in health and comfort to keep them healthy, strong and happy. Our products are designed for horses, livestock, goats, cattle and sheep, small caged animals, rabbits, guinea pigs and more.</p>
  </div>
  <div class="btn abs" style="left:588px;top:1208px;width:97px;height:25px">Get A Quote</div>
</section>

<section class="band abs">
  <h2 class="title abs" style="left:172px;top:110px">Clean, dry, natural solution</h2>
  <div class="body abs" style="left:172px;top:152px;width:430px">
    <p>For many people their animals, whether it be a horse, goat or other are more than just an animal; they are a part of your family, a way of life, and their comfort is important. Fine cut 100% chopped straw offers a softer bedding for your equine or other large and/or small animal.</p>
    <p>This straw bedding is light weight which allows for easier spreading, removing and hauling away. Straw also decomposes a lot faster than wood shavings and makes for great compost material.</p>
  </div>
  <ul class="list abs" style="left:172px;top:270px">
    <li>100% Natural Chopped Straw</li><li>Low Dust</li><li>Chemical &amp; Additive Free</li><li>Clean &amp; Highly Absorbent</li><li>Cheaper than Wood Shavings</li><li>Economic – less used and less wasted</li><li>Environmentally Friendly – Recyclable &amp; Compostable</li>
  </ul>
  <div class="btn abs" style="left:172px;top:437px;width:97px;height:25px">Get A Quote</div>
  <div class="photo abs" style="left:662px;top:106px;width:364px;height:364px;background:linear-gradient(#8a5a2e,#5e3a1b 50%,#9a6b3c)" role="img" aria-label="Indoor riding arena with timber roof trusses"></div>
</section>

<section class="feed">
  <div class="photo abs" style="left:172px;top:2043px;width:366px;height:365px;background:linear-gradient(90deg,#7a5c44,#c9c1b4 55%,#5e4737)" role="img" aria-label="Goats feeding along a barn pen rail"></div>
  <h2 class="title abs" style="left:588px;top:2057px">Our Feed</h2>
  <div class="body abs" style="left:588px;top:2100px;width:438px">
    <p>Hay cubes and pellets are made from premium hay offering a variety of animals a feed that is non GMO and packed with natural nutrients. These pellets and cubes are fed easily to handle, store and ship. As well, they reduce the amount of wasted feed.</p>
  </div>
  <ul class="list abs" style="left:588px;top:2158px">
    <li>100% Natural</li><li>Chemical &amp; Additive Free</li><li>Available in Pellets or Cubes</li><li>High Protein Content</li><li>Eliminate Waste in Feeding</li><li>Clean – Eliminates Dust from Feeding Baled Hay</li><li>Cost Effective</li><li>Convenient</li><li>Less wasted feed</li>
  </ul>
  <div class="btn abs" style="left:588px;top:2366px;width:97px;height:25px">Get A Quote</div>

  <div class="arrow abs" style="left:112px;top:2580px">‹</div>
  <div class="card abs" style="left:172px;width:197px"><div class="pack" role="img" aria-label="Feed bag"></div><h4>Product Name</h4><div class="stars">★★★★★</div><div class="price">$100.00</div></div>
  <div class="card abs" style="left:390px;width:197px"><div class="pack" role="img" aria-label="Feed bag"></div><h4>Product Name</h4><div class="stars">★★★★★</div><div class="price">$100.00</div></div>
  <div class="card hover abs" style="left:628px;width:167px;top:2476px;height:242px">
    <div class="pack" role="img" aria-label="Feed bag"></div>
    <div class="zoom abs"><svg width="56" height="56" viewBox="0 0 56 56"><circle cx="26" cy="26" r="9" fill="none" stroke="#f7941d" stroke-width="2"/><path d="M32 32l7 7M26 22v8M22 26h8" stroke="#f7941d" stroke-width="2"/></svg></div>
    <h4 style="margin-top:10px">Product Name</h4><div class="stars">★★★★★</div><div class="price">$100.00</div>
  </div>
  <div class="card abs" style="left:828px;width:198px"><div class="pack" role="img" aria-label="Feed bag"></div><h4>Product Name</h4><div class="stars">★★★★★</div><div class="price">$100.00</div></div>
  <div class="arrow abs" style="left:1080px;top:2580px">›</div>
</section>

<section class="clients abs" role="img" aria-label="Sheep in a field, softly blurred background">
  <h2>Whats Our Clients Says</h2>
  <div class="who">Mara Delton</div>
  <div class="role">Managing Member, Northgate Holdings</div>
  <p class="quote">Lorem ipsum is simply dummy text of the printing and typesetting industry. Lorem Ipsum has been the industry's standard dummy text ever since the 1500s, when an unknown printer took a galley of type and scrambled it to make a type specimen book. It has survived not only five centuries, but also the leap into electronic typesetting, remaining essentially unchanged.</p>
  <div class="dots"><span></span><span></span><span class="on"></span></div>
  <div class="arrow abs" style="left:245px;top:230px;color:#fff">‹</div>
  <div class="arrow abs" style="left:943px;top:230px;color:#fff">›</div>
</section>

<footer class="footer">
  <div class="brand abs" style="left:172px;top:3360px;font-size:15px"><span class="brand-dot" style="width:22px;height:22px"></span>GOLDFIELD BEDDING</div>
  <p class="body abs" style="left:172px;top:3412px;width:160px;font-size:8px;line-height:1.45">Ready to start a new project or curious about your next step? Drop us a note to talk about what we can offer and let us help you plan your next project today.</p>
  <div class="abs" style="left:434px;top:3340px"><h5>Menu</h5><div class="links">Home<br>About us<br>Feed<br>Bedding<br>Contact</div></div>
  <div class="abs" style="left:603px;top:3340px"><h5>Contact Us</h5><div class="links" style="line-height:14px">Goldfield Bedding<br>PO Box 12 Main Street<br>Millbrook, ON<br><span style="line-height:26px">555-010-2040</span><br>info@goldfieldbedding.com</div></div>
  <div class="abs" style="left:829px;top:3340px;width:197px">
    <h5>Social Media</h5>
    <div class="social" style="margin-top:15px"><span></span><span></span><span></span><span></span><span></span></div>
    <div class="field-sm" style="margin-top:22px">Email Address</div>
    <div class="btn" style="margin-top:8px;height:27px;font-size:9px">Subscribe Now</div>
  </div>
  <div class="abs" style="left:172px;top:3515px;width:854px;height:1px;background:#eeeeee"></div>
  <div class="copy abs">©2021 goldfieldbedding. All Rights Reserved.</div>
</footer>

<div class="shade abs"></div>

<div class="modal abs" role="dialog" aria-label="Request a Quote">
  <h2>Request a Quote</h2>
  <svg class="close abs" width="16" height="16" viewBox="0 0 16 16"><path d="M2 2l12 12M14 2L2 14" stroke="#111" stroke-width="2"/></svg>
  <div class="input abs" style="left:39px;top:94px;width:380px;height:38px">First Name*</div>
  <div class="input abs" style="left:437px;top:94px;width:380px;height:38px">Last Name*</div>
  <div class="input abs" style="left:39px;top:144px;width:380px;height:38px">Email Address*</div>
  <div class="input abs" style="left:437px;top:144px;width:380px;height:38px">Contact Number*</div>
  <div class="input abs" style="left:39px;top:194px;width:778px;height:139px">Requirements*</div>
  <div class="btn abs" style="left:336px;top:354px;width:197px;height:36px;font-size:12px;font-weight:600">Send Message</div>
</div>

</body>
</html>
```